Grey Fennel Medical Website to make connecting and communicating easier

To create a unique, user-friendly, professional website for patients and professionals to access education/ information, forms, appointments, contact details, and data about us, and for us to have the capacity to link to various cloud-based platforms.
To use the logo design and colour scheme we have just sourced.

WEBSITE to be eye catching, Inspiring and alluring
- efficient and logical
- professional and trustworthy appearance
- health focus "living health matters"
- user friendly
- ability to link with cloud-based software and video conferencing tools/ telehealth
- colours- black/ white teal and ?silver

PAGES:
page 1 - Our clinic and staff, services offered, contact us- address/ map / contact details- social media connections
page 2- patients and visitors - New patient forms to complete, news and patient informtion (educatinal)
page 3 - health professionals -referral forms, research and education
page 3- online appointments
page 4 - Quick links - partners, other services
page 5- privacy policy, disclaimer

HI, Could we please extend the deadline another 5 days, so sorry just struggling with my workload to be able to keep up and I am wanting to liaise more with the designer that I will choose. I am so happy with SketchHarbor and all the designers - thank you! Thank you so much!!

Target Market(s)

Patients - mostly over 60's so the website must be minimal clicks and simple to navigate
Professionals - for education and access forms

Industry/Entity Type

Health Care

Coding

Coded - Design and coding required

Number of Pages Required

5+ page

Font styles to use
Sans Serif
Script

Colors
33b8a4
86cfc6

Requirements
Must have
• WEBSITE to be eye catching, Inspiring and alluring
- efficient and logical
- user friendly

WEBSITE - professional and user friendly
- ability to link with cloud based software and videoconferencing/ telehealth
Nice to have
• clean and crisp presentation
happy for an innovative look
room to add more services and ability to link pages and resources
Should not have
• Please ensure the website is not:
clunky
difficult to navigate
common and cheap looking

```html
<!DOCTYPE html>
<html lang="en">
<head>
<meta charset="utf-8">
<title>Grey Fennel Medical</title>
<link rel="stylesheet" href="https://fonts.googleapis.com/css2?family=Cinzel:wght@700&family=Open+Sans:wght@400;600;700&display=swap">
<style>
:root{
  --teal:#23ad97;
  --teal-light:#86cfc6;
  --ink:#1d1d1d;
  --body:#444;
  --grey-bg:#f2f2f2;
  --white:#fff;
  --black:#000;
}
*{box-sizing:border-box;margin:0;padding:0}
html,body{width:1200px;height:3241px;overflow:hidden}
body{font-family:"Open Sans",Arial,sans-serif;color:var(--body);background:var(--white);position:relative}
.serif{font-family:"Cinzel",Georgia,serif;font-weight:700}

/* header */
.site-header{position:absolute;left:0;top:0;width:1200px;height:130px;background:var(--white)}
.brand{position:absolute;left:112px;top:36px;display:flex;align-items:center;gap:10px}
.brand-dot{width:38px;height:38px;border-radius:50%;background:var(--teal);flex:none}
.brand-name{font-weight:700;font-size:20px;color:var(--teal);line-height:1.1;width:130px}
.btn-appoint{position:absolute;left:850px;top:20px;width:238px;height:40px;border-radius:20px;background:var(--teal);color:var(--white);font-weight:700;font-size:15px;display:flex;align-items:center;justify-content:center}
.main-nav{position:absolute;right:110px;top:81px;display:flex;gap:22px;font-size:12px;color:var(--ink)}
.main-nav .active{color:var(--teal);font-weight:600;border-bottom:2px solid var(--teal);padding-bottom:8px}

/* hero */
.hero{position:absolute;left:0;top:130px;width:1200px;height:665px;background:radial-gradient(ellipse at 70% 40%,#7b8583 0%,#5f6a68 45%,#45504f 100%)}
.hero-title{position:absolute;left:0;width:1200px;top:250px;text-align:center;font-size:64px;color:var(--white);letter-spacing:1px}
.hero-sub{position:absolute;left:0;width:1200px;top:325px;text-align:center;font-size:22px;color:var(--white)}
.btn-hero{position:absolute;left:520px;top:378px;width:160px;height:56px;border-radius:28px;background:var(--white);color:var(--teal);font-weight:600;font-size:15px;display:flex;align-items:center;justify-content:center}
.dots{position:absolute;left:570px;top:626px;display:flex;gap:7px}
.dots span{width:9px;height:9px;border-radius:50%;background:var(--white)}
.dots span:first-child{background:none;border:1.5px solid var(--white)}

/* about */
.about{position:absolute;left:0;top:795px;width:1200px;height:473px;background:var(--teal)}
.about h2{position:absolute;left:112px;top:52px;font-size:37px;color:var(--white)}
.about .text{position:absolute;left:112px;top:112px;width:480px;font-size:13.5px;line-height:25px;color:var(--white)}
.about .text p+p{margin-top:12px}
.btn-outline-white{position:absolute;left:112px;top:334px;width:171px;height:50px;border:2px solid var(--white);border-radius:25px;color:var(--white);font-weight:600;font-size:15px;display:flex;align-items:center;justify-content:center}
.about-photo{position:absolute;left:642px;top:70px;width:447px;height:325px;border:4px solid var(--teal-light);background:linear-gradient(160deg,#eef1f4 0%,#c7d0d8 50%,#7d8c99 100%)}

/* services */
.services{position:absolute;left:0;top:1268px;width:1200px;height:595px;background:var(--grey-bg)}
.services h2{position:absolute;left:0;width:1200px;top:68px;text-align:center;font-size:37px;color:var(--ink)}
.service{position:absolute;top:156px;width:230px;text-align:center}
.service .ring{width:126px;height:126px;margin:0 auto;border:2px solid var(--teal);border-radius:50%;display:flex;align-items:center;justify-content:center}
.service h3{margin-top:20px;font-size:15px;font-weight:700;color:var(--ink)}
.service p{margin-top:8px;font-size:12.5px;line-height:21.5px;color:var(--body)}
.btn-outline-teal{margin:18px auto 0;width:128px;height:40px;border:2px solid var(--teal);border-radius:20px;color:var(--teal);font-size:13px;display:flex;align-items:center;justify-content:center}
.chev{position:absolute;top:210px}

/* clinic */
.clinic{position:absolute;left:0;top:1863px;width:1200px;height:504px;background:var(--white)}
.clinic-photo{position:absolute;left:112px;top:68px;width:441px;height:366px;border:1px solid #ddd;padding:6px;background:var(--white);box-shadow:0 0 4px rgba(0,0,0,.12)}
.clinic-photo div{width:100%;height:100%;background:linear-gradient(110deg,#f1f3f5 0%,#d9e0e6 45%,#a9bccd 75%,#5f84b4 100%)}
.clinic h2{position:absolute;left:597px;top:86px;font-size:37px;color:var(--ink)}
.clinic .text{position:absolute;left:599px;top:142px;width:496px;font-size:15.3px;line-height:23px;color:var(--body)}
.clinic .text p+p{margin-top:10px}
.btn-teal{position:absolute;left:599px;top:348px;width:152px;height:48px;border-radius:24px;background:var(--teal);color:var(--white);font-weight:600;font-size:15px;display:flex;align-items:center;justify-content:center}

/* contact */
.contact{position:absolute;left:0;top:2367px;width:1200px;height:564px;background:var(--grey-bg)}
.contact h2{position:absolute;left:0;width:1200px;top:52px;text-align:center;font-size:37px;color:var(--ink)}
.contact .lead{position:absolute;left:0;width:1200px;top:102px;text-align:center;font-size:16px;color:var(--body)}
.field{position:absolute;background:var(--white);border:1px solid #cfcfcf;font-size:14px;color:#555;padding:10px 13px}
.btn-submit{position:absolute;left:112px;top:441px;width:152px;height:44px;border-radius:22px;background:var(--teal);color:var(--white);font-weight:700;font-size:15px;display:flex;align-items:center;justify-content:center}
.map{position:absolute;left:633px;top:158px;width:454px;height:339px;border:3px solid var(--white);background:linear-gradient(135deg,#f0ece4,#e6e1d6 55%,#dbe6d6)}

/* footer */
.site-footer{position:absolute;left:0;top:2931px;width:1200px;height:310px;background:var(--black)}
.footer-brand{position:absolute;left:112px;top:70px;display:flex;align-items:center;gap:10px}
.socials{position:absolute;left:112px;top:174px;display:flex;gap:6px}
.socials span{width:36px;height:36px;border-radius:50%;background:var(--teal)}
.quick h4{position:absolute;left:516px;top:80px;font-size:16px;color:var(--white)}
.quick a{position:absolute;font-size:13px;color:#bdbdbd;text-decoration:none}
.copyright{position:absolute;left:0;width:1200px;top:268px;text-align:center;font-size:12px;color:#ccc}
</style>
</head>
<body>

<header class="site-header">
  <div class="brand"><span class="brand-dot"></span><span class="brand-name">Grey Fennel Medical</span></div>
  <div class="btn-appoint">ONLINE APPOINTMENTS</div>
  <nav class="main-nav">
    <span class="active">HOME</span><span>ABOUT US</span><span>OUR CLINIC AND STAFF</span><span>SERVICES</span><span>PATIENTS AND VISITORS</span><span>HEALTH PROFESSIONAL</span><span>CONTACT</span>
  </nav>
</header>

<section class="hero" role="img" aria-label="Doctor holding a tablet with overlaid medical hexagon icons">
  <h1 class="hero-title serif">GREY FENNEL MEDICAL</h1>
  <p class="hero-sub">Excepteur sint occaecat cupidatat non proident sunt in culpa qui officia</p>
  <div class="btn-hero">CONTACT US</div>
  <div class="dots"><span></span><span></span><span></span><span></span></div>
</section>

<section class="about">
  <h2 class="serif">ABOUT US</h2>
  <div class="text">
    <p>Lorem ipsum dolor sit amet, consectetur adipiscing elit, sed do eiusmod tempor incididunt ut labore et dolore magna aliqua. Ut enim ad minim veniam, quis nostrud exercitation ullamco laboris nisi ut aliquip ex ea commodo consequat.</p>
    <p>Sed ut perspiciatis unde omnis iste natus error sit voluptatem accusantium doloremque laudantium, totam rem aperiam, eaque ipsa quae ab illo inventore veritatis et quasi architecto beatae vitae dicta sunt explicabo</p>
  </div>
  <div class="btn-outline-white">LEARN MORE</div>
  <div class="about-photo" role="img" aria-label="Stethoscope on a clipboard beside a laptop"></div>
</section>

<section class="services">
  <h2 class="serif">GREY FENNEL MEDICAL SERVICES</h2>
  <svg class="chev" style="left:46px" width="24" height="44" viewBox="0 0 24 44"><path d="M20 4 4 22l16 18" fill="none" stroke="#999" stroke-width="5"/></svg>
  <svg class="chev" style="left:1118px" width="24" height="44" viewBox="0 0 24 44"><path d="M4 4l16 18L4 40" fill="none" stroke="#999" stroke-width="5"/></svg>

  <div class="service" style="left:105px">
    <div class="ring"><svg width="56" height="56" viewBox="0 0 56 56" fill="none" stroke="#23ad97" stroke-width="2.5"><path d="M28 44S10 32 10 20a9 9 0 0 1 18-3 9 9 0 0 1 18 3c0 12-18 24-18 24z"/><path d="M14 26h8l3-6 4 10 3-4h10"/></svg></div>
    <h3>OCCAECAT CUPIDATAT</h3>
    <p>Temporibus autem quibusdam et aut officiis debitis aut rerum necessitatibus saepe eveniet ut et voluptates sint et molestiae non recusandae. Itaque earum rerum hic tenetur a sapiente reiciendis voluptatibus delectus.</p>
    <div class="btn-outline-teal">LEARN MORE</div>
  </div>
  <div class="service" style="left:359px">
    <div class="ring"><svg width="56" height="56" viewBox="0 0 56 56" fill="none" stroke="#23ad97" stroke-width="2.5"><path d="M28 8l16 6v12c0 11-8 18-16 22-8-4-16-11-16-22V14z"/><path d="M20 28l6 6 11-12"/></svg></div>
    <h3>NUMQUAM EIUS</h3>
    <p>Temporibus autem quibusdam et aut officiis debitis aut rerum necessitatibus saepe eveniet ut et voluptates sint et molestiae non recusandae. Itaque earum rerum hic tenetur a sapiente reiciendis voluptatibus delectus.</p>
    <div class="btn-outline-teal">LEARN MORE</div>
  </div>
  <div class="service" style="left:612px">
    <div class="ring"><svg width="56" height="56" viewBox="0 0 56 56" fill="none" stroke="#23ad97" stroke-width="2.5"><circle cx="28" cy="28" r="16"/><path d="M28 20v16M20 28h16"/></svg></div>
    <h3>TEMPORA INCIDUNT</h3>
    <p>Temporibus autem quibusdam et aut officiis debitis aut rerum necessitatibus saepe eveniet ut et voluptates sint et molestiae non recusandae. Itaque earum rerum hic tenetur a sapiente reiciendis voluptatibus delectus.</p>
    <div class="btn-outline-teal">LEARN MORE</div>
  </div>
  <div class="service" style="left:866px">
    <div class="ring"><svg width="56" height="56" viewBox="0 0 56 56" fill="none" stroke="#23ad97" stroke-width="2.5"><path d="M8 28 28 10l20 18"/><path d="M14 24v22h28V24"/><path d="M24 46V34h8v12"/></svg></div>
    <h3>VOLUPTATE VELIT</h3>
    <p>Temporibus autem quibusdam et aut officiis debitis aut rerum necessitatibus saepe eveniet ut et voluptates sint et molestiae non recusandae. Itaque earum rerum hic tenetur a sapiente reiciendis voluptatibus delectus.</p>
    <div class="btn-outline-teal">LEARN MORE</div>
  </div>
</section>

<section class="clinic">
  <div class="clinic-photo"><div role="img" aria-label="Medical staff in white coats standing with arms crossed"></div></div>
  <h2 class="serif">OUR CLINIC AND STAFF</h2>
  <div class="text">
    <p>But I must explain to you how all this mistaken idea of denouncing pleasure and praising pain was born and I will give you a complete account of the system, and expound the actual teachings of the great explorer of the truth, the master-builder of human happiness.</p>
    <p>But who has any right to find fault with a man who chooses to enjoy a pleasure that has no annoying consequences, or one who avoids a pain that produces no resultant pleasure.</p>
  </div>
  <div class="btn-teal">LEARN MORE</div>
</section>

<section class="contact">
  <h2 class="serif">CONTACT US</h2>
  <p class="lead">Please use the contact form below to get in touch.</p>
  <div class="field" style="left:112px;top:169px;width:239px;height:40px">First name</div>
  <div class="field" style="left:361px;top:169px;width:239px;height:40px">Last name</div>
  <div class="field" style="left:112px;top:220px;width:488px;height:40px">Your email</div>
  <div class="field" style="left:112px;top:272px;width:488px;height:40px">Phone</div>
  <div class="field" style="left:112px;top:323px;width:488px;height:95px">Your message</div>
  <div class="btn-submit">SUBMIT NOW</div>
  <div class="map" role="img" aria-label="Street map showing the clinic location"></div>
</section>

<footer class="site-footer">
  <div class="footer-brand"><span class="brand-dot"></span><span class="brand-name">Grey Fennel Medical</span></div>
  <div class="socials" aria-label="Social media links"><span></span><span></span><span></span></div>
  <div class="quick">
    <h4 class="serif">QUICK LINKS</h4>
    <a style="left:516px;top:117px">Partners</a>
    <a style="left:516px;top:142px">Other services</a>
    <a style="left:742px;top:117px">Privacy Policy</a>
    <a style="left:742px;top:142px">Disclaimer</a>
    <a style="left:962px;top:117px">Health Professionals</a>
    <a style="left:962px;top:142px">Online Appointments</a>
  </div>
  <p class="copyright">Copyrights © 2020, Grey Fennel Medical. All rights reserved.</p>
</footer>

</body>
</html>
```